Home Accessibility

Sturdy Haven Builders (SHB) is a specialty construction company specializing in building custom homes and home modifications for individuals that are “Aging in Place” or with disabilities.
SHB is a full service construction company specializing in making independence accessible by helping people plan for now and the future. We provide a number of building services from custom designing a new home to modifying an existing home. SHB is a Registered Lifelong Dwelling Expert (RLDE). As a RLDE specialist, SHB is able to offer specialized strategies and techniques for designing and building aesthetically enriching living environments.
Marcus has been in the building industry for over 18 years; He has served on the board of the Residential Crafters Guild. He is Registered Lifelong Dwelling Expert (RLDE). Certified, also as Eco Structures for Trade Practitioners and a member of the Fair Trade Registry (FTR)

I am looking for a promo piece where we install 2- 24" Talvo grab bars for $149.00
We can also do a free home evaluation which will show what or if any other modification or feature would be beneficial to them and the home.

Target Market(s)

Age 65+, disable, children of 65+

Industry/Entity Type

Construction

Requirements
Nice to have
• I would like to incorporate some or all of the bullet points from my mailer

```html
<!DOCTYPE html>
<html lang="en">
<head>
<meta charset="utf-8">
<title>Sturdy Haven Builders – Mailer Back</title>
<link rel="stylesheet" href="https://fonts.googleapis.com/css2?family=Source+Sans+3:wght@400;600;700&family=Roboto+Condensed:wght@400;700&family=Arimo&display=swap">
<style>
  :root {
    --paper: #ffffff;
    --ink: #111111;
    --navy: #1b2456;
    --accent: #c8202c;
    --rule: #222222;
    --gap: #ffffff;
  }
  * { margin: 0; padding: 0; box-sizing: border-box; }
  html, body { width: 1200px; height: 930px; overflow: hidden; background: var(--paper); }
  .mailer { position: relative; width: 1200px; height: 930px; background: var(--paper); color: var(--ink); }

  .feature-strip { position: absolute; left: 0; top: 0; width: 338px; height: 930px; background: var(--gap); }
  .feature { position: absolute; left: 0; width: 338px; }
  .feature-title {
    position: absolute; right: 18px; top: 14px; text-align: right;
    font-family: "Source Sans 3", sans-serif; font-weight: 700; font-size: 22px; line-height: 28px;
    color: #fff; text-shadow: 1px 1px 3px rgba(0,0,0,.85);
  }
  .feature--living .feature-title { top: 44px; }
  .feature--living  { top: 0;   height: 228px; background: linear-gradient(160deg, #e8c08a 0%, #c7813f 45%, #8a4e22 100%); }
  .feature--bath    { top: 233px; height: 227px; background: linear-gradient(180deg, #e9e3d8 0%, #d59a5c 55%, #b8733a 100%); }
  .feature--kitchen { top: 465px; height: 228px; background: linear-gradient(170deg, #c9cdd1 0%, #6e6a66 50%, #3a2e27 100%); }
  .feature--house   { top: 698px; height: 232px; background: linear-gradient(180deg, #9fc4e4 0%, #d8dccf 50%, #a4a88e 80%, #5d7d3c 100%); }

  .about {
    position: absolute; left: 402px; top: 115px; width: 290px;
    font-family: "Source Sans 3", sans-serif; font-size: 22px; line-height: 28.7px; color: var(--ink);
  }
  .brand {
    position: absolute; left: 446px; top: 672px; display: flex; align-items: center; gap: 12px;
    font-family: "Source Sans 3", sans-serif; font-weight: 700; font-size: 60px; line-height: 80px; color: var(--navy);
  }
  .brand-dot { width: 24px; height: 24px; border-radius: 50%; background: var(--navy); }

  .postage {
    position: absolute; left: 932px; top: 50px; width: 207px; height: 164px;
    border: 2px solid var(--rule);
    font-family: "Arimo", sans-serif; font-size: 23px; line-height: 31px; text-align: center; padding-top: 4px;
  }
  .postage-class {
    position: absolute; left: 932px; top: 234px; width: 207px; text-align: center;
    font-family: "Arimo", sans-serif; font-size: 24px;
  }

  .offer {
    position: absolute; left: 733px; top: 284px; width: 406px; text-align: center;
    font-family: "Roboto Condensed", sans-serif; color: var(--navy);
  }
  .offer-deal { font-weight: 700; font-size: 24px; line-height: 30px; }
  .offer-price { color: var(--accent); }
  .offer-extra { font-size: 20px; line-height: 28px; color: var(--ink); }

  .address {
    position: absolute; left: 733px; top: 378px; width: 406px; height: 138px;
    border: 2px solid var(--rule); font-family: "Arimo", sans-serif; font-size: 19px; line-height: 25px;
  }
  .address-route { position: absolute; left: 68px; top: 12px; font-size: 16px; }
  .address-lines { position: absolute; left: 22px; top: 70px; }

  .contact { position: absolute; left: 830px; top: 630px; font-family: "Roboto Condensed", sans-serif; font-style: normal; }
  .contact-name { font-weight: 700; font-size: 31px; line-height: 42px; }
  .contact-line { font-size: 26px; line-height: 36px; }
</style>
</head>
<body>
<main class="mailer">
  <section class="feature-strip">
    <div class="feature feature--living" role="img" aria-label="Photo of a bright wood-panelled living room with sofa and armchairs">
      <p class="feature-title">Accessing The Home</p>
    </div>
    <div class="feature feature--bath" role="img" aria-label="Photo of a tiled bathroom with corner tub and glass shower">
      <p class="feature-title">Accessing The Bedroom<br>and Bathroom</p>
    </div>
    <div class="feature feature--kitchen" role="img" aria-label="Photo of a modern kitchen with steel counters and range">
      <p class="feature-title">Accessing the Kitchen</p>
    </div>
    <div class="feature feature--house" role="img" aria-label="Photo of a two-storey craftsman house with front porch">
      <p class="feature-title">Planning for Future<br>Independence</p>
    </div>
  </section>

  <p class="about">SHB is a Registered Lifelong Dwelling Expert (RLDE) with specialized strategies and techniques for designing and building aesthetically enriching living environments.<br>Marcus has been in the building industry for over 18 years; Serving on the board of the Residential Crafters Guild and Registered Lifelong Dwelling Expert (RLDE). Certified, also as Eco Structures for Trade Practitioners and a member of the Fair Trade Registry (FTR).</p>

  <div class="brand"><span class="brand-dot"></span>SHB</div>

  <div class="postage">PRSRT STD<br>U.S. POSTAGE<br>PAID<br>CITY, STATE<br>PERMIT NO. XXX</div>
  <p class="postage-class">ECRWSS</p>

  <section class="offer">
    <p class="offer-deal">Two 24" Talvo Grab Bars Installed <span class="offer-price">$149.00</span></p>
    <p class="offer-extra">Plus a FREE Home Evaluation</p>
  </section>

  <div class="address">
    <p class="address-route">*********ECRWSSEDDM****</p>
    <p class="address-lines">Residential Customer<br>City, State 5-Digit ZIP Code</p>
  </div>

  <address class="contact">
    <p class="contact-name">Marcus Delbrook</p>
    <p class="contact-line">Ph: 555-014-2270</p>
    <p class="contact-line">Fax: 555-014-2281</p>
    <p class="contact-line">Email: info@shbhomes.com</p>
    <p class="contact-line">Web: www.shbhomes.com</p>
  </address>
</main>
</body>
</html>
```